Construction Company Cellar Crafters needs Business Card

I would like modern looking business card design. I am attaching logo of our company. Please include cell nr 302.418.7650 , email address cellarcrafters4u@examplemail.com, web : cellarcrafters4u.com, please also include wording: Specializing in finishing and remodeling basements. You can play with dark grey and orange colors or any ideas are welcome. Also include social media icons Friendloop and HouseGuidr.

```html
<!DOCTYPE html>
<html lang="en">
<head>
<meta charset="utf-8">
<title>Cellar Crafters — Business Card</title>
<link href="https://fonts.googleapis.com/css2?family=Orbitron:wght@500;600&family=Open+Sans:wght@400;600&display=swap" rel="stylesheet">
<style>
  :root {
    --bg: #e9e6e1;
    --card-dark: #0d0d0d;
    --card-dark-2: #1a1a1a;
    --orange: #f05a28;
    --white: #ffffff;
    --rule-grey: #d9dde0;
    --shadow: rgba(0, 0, 0, 0.25);
  }
  * { box-sizing: border-box; margin: 0; padding: 0; }
  html, body {
    width: 1200px; height: 900px; overflow: hidden;
    background: var(--bg);
  }
  .canvas { position: relative; width: 1200px; height: 900px; }

  .card {
    position: absolute;
    width: 700px; height: 400px;
    overflow: hidden;
    border-radius: 3px;
    box-shadow: 0 14px 30px var(--shadow);
    background: radial-gradient(ellipse at 50% 30%, var(--card-dark-2), var(--card-dark) 70%);
  }
  .card--front { left: 110px; top: 50px; }
  .card--back  { left: 390px; top: 450px; }

  .brand {
    position: absolute; left: 0; right: 0;
    font-family: "Orbitron", sans-serif; font-weight: 600;
    color: var(--orange);
    white-space: nowrap;
    letter-spacing: 2px;
    font-size: 36px;
    display: flex; align-items: center; justify-content: center; gap: 14px;
  }
  .brand__mark { width: 22px; height: 22px; background: var(--orange); }
  .card--front .brand { top: 100px; }
  .card--back  .brand { top: 70px; }

  /* front */
  .tagline-band {
    position: absolute; left: 0; right: 0; bottom: 0; height: 150px;
    background: var(--orange);
    display: flex; align-items: center; justify-content: center;
  }
  .tagline {
    font-family: "Orbitron", sans-serif; font-weight: 500;
    color: var(--white);
    font-size: 18px; line-height: 1.6;
    text-align: center; letter-spacing: 1.5px;
    text-transform: uppercase;
  }

  /* back */
  .divider {
    position: absolute; left: 0; right: 0; top: 222px; height: 10px;
    background: var(--rule-grey);
  }
  .contact-band {
    position: absolute; left: 0; right: 0; top: 232px; bottom: 0;
    background: var(--orange);
  }
  .person {
    position: absolute; right: 36px; top: 150px; text-align: right;
  }
  .person__name {
    font-family: "Orbitron", sans-serif; font-weight: 500; color: var(--white);
    font-size: 18px; letter-spacing: 1.5px; text-transform: uppercase;
  }
  .person__role {
    font-family: "Open Sans", sans-serif; color: var(--white);
    font-size: 14px; margin-top: 4px;
  }
  .social {
    position: absolute; right: 36px; top: 248px;
    display: flex; gap: 16px;
  }
  .social__item {
    display: flex; align-items: center; gap: 6px;
    font-family: "Open Sans", sans-serif; font-weight: 600;
    font-size: 13px; color: var(--white);
  }
  .social__dot { width: 14px; height: 14px; background: var(--white); border-radius: 2px; }

  .contact-list {
    position: absolute; left: 36px; bottom: 30px;
    list-style: none;
  }
  .contact-list li {
    display: flex; align-items: center; gap: 12px;
    font-family: "Open Sans", sans-serif; color: var(--white);
    font-size: 19px; line-height: 1.5;
  }
  .contact-list svg { width: 15px; height: 15px; flex: none; }
</style>
</head>
<body>
<main class="canvas">

  <section class="card card--front" aria-label="Business card front">
    <div class="brand"><span class="brand__mark"></span>CELLAR CRAFTERS</div>
    <div class="tagline-band">
      <p class="tagline">Specializing in finishing and<br>remodeling basements.</p>
    </div>
  </section>

  <section class="card card--back" aria-label="Business card back">
    <div class="brand"><span class="brand__mark"></span>CELLAR CRAFTERS</div>
    <div class="divider"></div>
    <div class="contact-band"></div>

    <div class="person">
      <p class="person__name">Marcus Hale</p>
      <p class="person__role">Managing Director</p>
    </div>

    <div class="social">
      <span class="social__item"><span class="social__dot"></span>Friendloop</span>
      <span class="social__item">HouseGuidr</span>
    </div>

    <ul class="contact-list">
      <li>
        <svg viewBox="0 0 16 16" aria-hidden="true"><rect x="4" y="1" width="8" height="14" rx="1.5" fill="none" stroke="#fff" stroke-width="1.6"/><circle cx="8" cy="12.3" r="0.9" fill="#fff"/></svg>
        302.418.7650
      </li>
      <li>
        <svg viewBox="0 0 16 16" aria-hidden="true"><rect x="1" y="3" width="14" height="10" fill="#fff"/><path d="M1 3 L8 9 L15 3" fill="none" stroke="#f05a28" stroke-width="1.4"/></svg>
        cellarcrafters4u@examplemail.com
      </li>
      <li>
        <svg viewBox="0 0 16 16" aria-hidden="true"><circle cx="8" cy="8" r="6.5" fill="none" stroke="#fff" stroke-width="1.5"/><ellipse cx="8" cy="8" rx="2.8" ry="6.5" fill="none" stroke="#fff" stroke-width="1.2"/><line x1="1.5" y1="8" x2="14.5" y2="8" stroke="#fff" stroke-width="1.2"/></svg>
        cellarcrafters4u.com
      </li>
    </ul>
  </section>

</main>
</body>
</html>
```